Corportate Power Point Template

We need a corporate PPT Design for our startup Big Data company.

Basically, our company will ingest, analyze and generate dynamic Dashboards with data consumed from different sources like Social Networks, Enterprise Legacy Systems such as e-Commerce, ERP, CRM and others.

Company is headquartered in Brazil, but will have a global presence.

Industry/Entity Type

It Company

```html
<!DOCTYPE html>
<html lang="en">
<head>
<meta charset="utf-8">
<title>Project Title Here</title>
<link rel="stylesheet" href="https://fonts.googleapis.com/css2?family=Open+Sans:wght@600;700&family=Roboto+Condensed:wght@400;500&display=swap">
<style>
  :root {
    --orange: #f26a21;
    --orange-soft: #f9b98a;
    --peach: #fde3cf;
    --ink: #1c1c1c;
    --ink-soft: #2e2e2e;
    --paper: #ffffff;
    --footer-top: #ffffff;
    --footer-bottom: #e9e7e5;
  }
  * { margin: 0; padding: 0; box-sizing: border-box; }
  html, body { width: 1200px; height: 900px; overflow: hidden; background: var(--paper); }
  .slide {
    position: relative;
    width: 1200px;
    height: 900px;
    overflow: hidden;
    background: var(--paper);
  }
  .slide-backdrop {
    position: absolute;
    inset: 0 0 65px 0;
    background:
      radial-gradient(ellipse 900px 700px at 1150px 420px, var(--paper) 0%, rgba(255,255,255,0.9) 35%, rgba(255,255,255,0) 75%),
      linear-gradient(100deg, var(--orange-soft) 0%, var(--peach) 30%, #fff3ea 55%, var(--paper) 80%);
  }
  .brand {
    position: absolute;
    right: 42px;
    top: 362px;
    display: flex;
    align-items: center;
    gap: 16px;
    font-family: "Open Sans", Arial, sans-serif;
    font-weight: 700;
    font-size: 60px;
    letter-spacing: -1px;
    color: var(--orange);
    line-height: 1;
  }
  .brand-mark {
    width: 44px;
    height: 44px;
    background: var(--orange);
  }
  .project-title {
    position: absolute;
    right: 42px;
    top: 535px;
    font-family: "Open Sans", Arial, sans-serif;
    font-weight: 600;
    font-size: 54px;
    line-height: 1;
    color: var(--ink);
    text-align: right;
  }
  .project-title .accent { color: var(--orange); }
  .project-subtext {
    position: absolute;
    right: 42px;
    top: 628px;
    width: 700px;
    font-family: "Roboto Condensed", Arial, sans-serif;
    font-size: 25px;
    line-height: 36px;
    color: var(--ink-soft);
    text-align: right;
  }
  .slide-footer {
    position: absolute;
    left: 0;
    right: 0;
    bottom: 0;
    height: 65px;
    border-top: 3px solid var(--orange);
    background: linear-gradient(to bottom, var(--footer-top), var(--footer-bottom));
    display: flex;
    align-items: center;
    justify-content: space-between;
    padding: 0 15px 0 14px;
    font-family: "Roboto Condensed", Arial, sans-serif;
  }
  .copyright { font-size: 19px; font-weight: 500; color: var(--ink-soft); padding-top: 2px; }
  .page-number { font-size: 25px; font-weight: 500; color: var(--orange); padding-top: 2px; }
</style>
</head>
<body>
  <main class="slide">
    <div class="slide-backdrop" role="img" aria-label="Soft orange background with a receding dotted texture"></div>

    <div class="brand">
      <span class="brand-name">Crestline Data</span>
      <span class="brand-mark" aria-hidden="true"></span>
    </div>

    <h1 class="project-title"><span class="accent">Project</span> Title Here</h1>

    <p class="project-subtext">
      Subtext here Subtext here Subtext here Subtext here<br>
      Subtext here Subtext here Subtext here
    </p>

    <footer class="slide-footer">
      <span class="copyright">Copyright text here</span>
      <span class="page-number">Page 01</span>
    </footer>
  </main>
</body>
</html>
```